Business Cards

Need business card design that I can update for new employees and details. Needs to incorporate our logo, be bright and fun (in line with tourism and holidays)
Would like a Map of Western Australia on the front with locations all the caravan parks we own (just purchased Tom Price so please include that as well as others listed on our website).
Target Market(s)
Famillies
Contact Information for Business Card
5 Cards -
Neil Perrow (Director) e: perrow@wattlebay.com.au p: 0491 570 156
Mira Perrow (Director) e: perrow@wattlebay.com.au p: 0491 570 157
Owen Halvey (General Manager) e: halvey@wattlebay.com.au p: 0491 570 158
Helen Halvey (General Manager) e: halvey@wattlebay.com.au p: 0491 570 159
Colin Danby (Training and Operations Manager) - e: danby@wattlebay.com.au p:0491 570 110
Colors
Look and feel

```html
<!DOCTYPE html>
<html lang="en">
<head>
<meta charset="utf-8">
<title>Wattlebay Tourist Parks – Business Card</title>
<link rel="stylesheet" href="https://fonts.googleapis.com/css2?family=Marcellus&family=Lato:wght@400&display=swap">
<style>
  :root {
    --stage-top: #393939;
    --stage-bottom: #4e4e4e;
    --card-white: #ffffff;
    --ink-grey: #4b4b4b;
    --ink-black: #1e1e1e;
    --teal: #2fb5c6;
    --teal-bright: #45c2cd;
    --teal-soft: #6cbcaa;
    --paper-white: #ffffff;
  }
  * { margin: 0; padding: 0; box-sizing: border-box; }
  html, body {
    width: 1200px;
    height: 900px;
    overflow: hidden;
  }
  body {
    position: relative;
    background: linear-gradient(180deg, var(--stage-top) 0%, var(--stage-bottom) 100%);
    font-family: "Lato", Arial, sans-serif;
  }
  .card {
    position: absolute;
    top: 306px;
    width: 440px;
    height: 271px;
  }
  .card--back-side {
    left: 149px;
    background: var(--card-white);
  }
  .card--front-side {
    left: 608px;
    width: 441px;
    height: 272px;
    background: linear-gradient(160deg, var(--teal-bright) 0%, var(--teal-soft) 50%, var(--teal-bright) 100%);
  }
  .wordmark {
    position: absolute;
    font-family: "Marcellus", "Times New Roman", serif;
    font-weight: 400;
    text-transform: uppercase;
    line-height: 1;
  }
  .wordmark__name {
    display: block;
    font-size: 25px;
    letter-spacing: 3px;
  }
  .wordmark__name::first-letter {
    font-size: 40px;
  }
  .wordmark__tagline {
    display: block;
    font-size: 13px;
    letter-spacing: 3.2px;
    margin-top: 4px;
  }
  .card--back-side .wordmark {
    left: 22px;
    top: 38px;
    color: var(--ink-grey);
  }
  .card--back-side .wordmark__tagline {
    padding-left: 49px;
  }
  .card--front-side .wordmark {
    left: 0;
    right: 0;
    top: 140px;
    text-align: center;
    color: var(--paper-white);
  }
  .card--front-side .wordmark__name {
    font-size: 28px;
    letter-spacing: 3.6px;
  }
  .card--front-side .wordmark__name::first-letter {
    font-size: 46px;
  }
  .card--front-side .wordmark__tagline {
    font-size: 14px;
    letter-spacing: 3.6px;
    margin-top: 6px;
  }
  .staff {
    position: absolute;
    left: 24px;
    top: 152px;
  }
  .staff__name {
    font-family: "Marcellus", "Times New Roman", serif;
    font-size: 19px;
    font-weight: 400;
    color: var(--teal);
    text-transform: uppercase;
    letter-spacing: 0.3px;
    line-height: 1.1;
  }
  .staff__role {
    font-size: 12px;
    color: var(--ink-black);
    margin-top: 2px;
  }
  .contact {
    list-style: none;
    position: absolute;
    left: 23px;
    top: 203px;
  }
  .contact__item {
    display: flex;
    align-items: center;
    gap: 6px;
    font-size: 13px;
    color: var(--ink-black);
    height: 16px;
    margin-bottom: 4px;
  }
  .contact__icon {
    width: 16px;
    height: 16px;
    flex: none;
  }
</style>
</head>
<body>
  <section class="card card--back-side" aria-label="Card back with contact details">
    <h1 class="wordmark">
      <span class="wordmark__name">Wattlebay</span>
      <span class="wordmark__tagline">Tourist Parks</span>
    </h1>
    <div class="staff">
      <h2 class="staff__name">Neil Perrow</h2>
      <p class="staff__role">Director</p>
    </div>
    <ul class="contact">
      <li class="contact__item">
        <svg class="contact__icon" viewBox="0 0 16 16" aria-hidden="true">
          <rect width="16" height="16" fill="var(--teal)"/>
          <path d="M4.2 3.2c.4-.3.9-.3 1.2.1l1.2 1.6c.3.4.2.9-.1 1.2l-.7.6c.5 1.1 1.4 2 2.5 2.6l.6-.7c.3-.4.8-.4 1.2-.1l1.6 1.2c.4.3.4.8.1 1.2l-.8.9c-.5.5-1.3.6-2 .3C6.7 11 4.9 9.3 3.8 7c-.3-.7-.2-1.5.3-2z" fill="var(--paper-white)"/>
        </svg>
        <span>0491 570 156</span>
      </li>
      <li class="contact__item">
        <svg class="contact__icon" viewBox="0 0 16 16" aria-hidden="true">
          <rect width="16" height="16" fill="var(--teal)"/>
          <rect x="3" y="4.5" width="10" height="7" fill="none" stroke="var(--paper-white)" stroke-width="1"/>
          <path d="M3 4.5l5 4 5-4" fill="none" stroke="var(--paper-white)" stroke-width="1"/>
        </svg>
        <span>perrow@wattlebay.com.au</span>
      </li>
    </ul>
  </section>

  <section class="card card--front-side" aria-label="Card front">
    <h2 class="wordmark">
      <span class="wordmark__name">Wattlebay</span>
      <span class="wordmark__tagline">Tourist Parks</span>
    </h2>
  </section>
</body>
</html>
```